Quorva - corporate Business Card

We need a good look and innovative business card for a new start up company based in Los Angeles called "Quorva". We are in a payment business, including payment card, app, and ewallet. We are expert in online payment and Card not present (CNP) transaction.
We need an innovative, modern business card.

Our logo font is Aero Matics

Target Market(s)

Startup - Bank - Online Payment - Card Manufacturing

Industry/Entity Type

Startup

Contact Information for Business Card

phone: 555 014 7396 - Address: 4172 Marlowe blvd, Tessaly Park, OR 90299

Requirements
Must have
• Message: innovative, professional, expert, high tech, trust, online payment expert, security
Nice to have
• no comment
Should not have
• no Comment

```html
<!DOCTYPE html>
<html lang="en">
<head>
<meta charset="utf-8">
<title>Quorva – Business Card</title>
<link rel="stylesheet" href="https://fonts.googleapis.com/css2?family=Roboto:wght@400;500;700&display=swap">
<style>
  :root {
    --brand-red: #b81f2e;
    --ink: #2a2a2a;
    --card: #ffffff;
    --backdrop: #626a70;
  }
  * { box-sizing: border-box; margin: 0; padding: 0; }
  html, body { width: 1200px; height: 900px; overflow: hidden; }
  body {
    background: var(--backdrop);
    font-family: "Roboto", Arial, sans-serif;
    display: flex;
    align-items: center;
    justify-content: center;
    gap: 60px;
  }
  .card {
    position: relative;
    width: 500px;
    height: 286px;
    background: var(--card);
    border-radius: 14px;
    overflow: hidden;
    box-shadow: 0 10px 30px rgba(0,0,0,.35);
  }

  /* Front */
  .card-front .accent {
    position: absolute;
    background: var(--brand-red);
    height: 8px;
    width: 90px;
  }
  .card-front .accent-top { top: 0; left: 28px; border-radius: 0 0 4px 4px; }
  .card-front .accent-bottom { bottom: 0; right: 28px; border-radius: 4px 4px 0 0; }
  .card-front .brand {
    position: absolute;
    top: 92px;
    left: 0; right: 0;
    display: flex;
    align-items: center;
    justify-content: center;
    gap: 16px;
  }
  .brand-dot {
    width: 64px; height: 64px;
    border-radius: 50%;
    background: var(--brand-red);
  }
  .brand-name {
    color: var(--brand-red);
    font-weight: 700;
    font-size: 58px;
    letter-spacing: 1px;
    line-height: 1;
  }
  .card-front .website {
    position: absolute;
    bottom: 44px;
    left: 0; right: 0;
    text-align: center;
    font-size: 13px;
    color: var(--ink);
    letter-spacing: .3px;
  }

  /* Back */
  .card-back .brand {
    position: absolute;
    top: 26px; left: 30px;
    display: flex; align-items: center; gap: 8px;
  }
  .card-back .brand-dot { width: 36px; height: 36px; }
  .card-back .brand-name { font-size: 32px; }
  .person {
    position: absolute;
    top: 100px; left: 30px;
  }
  .person-name {
    color: var(--brand-red);
    font-size: 15px;
    font-weight: 700;
    text-transform: uppercase;
    letter-spacing: .4px;
  }
  .person-name .surname { font-weight: 400; }
  .person-role {
    font-size: 10px;
    color: var(--ink);
    letter-spacing: .5px;
    margin-top: 2px;
  }
  .divider {
    position: absolute;
    left: 30px; right: 30px;
    top: 146px;
    height: 1.5px;
    background: var(--brand-red);
  }
  .contacts {
    position: absolute;
    top: 156px; left: 30px;
    list-style: none;
    font-size: 11px;
    color: var(--ink);
    line-height: 16px;
  }
  .contacts li { display: flex; align-items: center; gap: 8px; }
  .contacts svg { width: 10px; height: 10px; fill: var(--brand-red); flex: none; }
  .address {
    position: absolute;
    right: 30px;
    top: 112px;
    text-align: left;
    font-size: 11.5px;
    color: var(--ink);
    line-height: 15px;
  }
</style>
</head>
<body>

  <section class="card card-front" aria-label="Card front">
    <span class="accent accent-top"></span>
    <div class="brand">
      <span class="brand-dot"></span>
      <span class="brand-name">Quorva</span>
    </div>
    <p class="website">www.quorvapay.com</p>
    <span class="accent accent-bottom"></span>
  </section>

  <section class="card card-back" aria-label="Card back">
    <div class="brand">
      <span class="brand-dot"></span>
      <span class="brand-name">Quorva</span>
    </div>

    <div class="person">
      <p class="person-name">Marcel <span class="surname">Dovan</span></p>
      <p class="person-role">FOUNDER</p>
    </div>

    <p class="address">4172 Marlowe blvd<br>Tessaly Park, OR 90299</p>

    <div class="divider"></div>

    <ul class="contacts">
      <li>
        <svg viewBox="0 0 10 10"><path d="M2 0.5l2 2-1 1.2c.6 1.3 1.6 2.3 2.9 2.9l1.2-1 2 2-1.3 1.6C4.5 9 1 5.5.5 1.8z"/></svg>
        555 014 7396
      </li>
      <li>
        <svg viewBox="0 0 10 10"><path d="M2.5 0h5a1 1 0 011 1v8a1 1 0 01-1 1h-5a1 1 0 01-1-1V1a1 1 0 011-1zm.3 1.2v6.6h4.4V1.2z"/></svg>
        555-014-7397
      </li>
      <li>
        <svg viewBox="0 0 10 10"><path d="M0 2h10v6H0zm1 .8L5 5.6 9 2.8v-.1L5 5 1 2.7z"/></svg>
        marcel@quorvapay.com
      </li>
      <li>
        <svg viewBox="0 0 10 10"><circle cx="5" cy="5" r="4.5"/><path d="M2 5h6M5 1.5v7" stroke="#fff" stroke-width=".8"/></svg>
        www.quorvapay.com
      </li>
    </ul>
  </section>

</body>
</html>
```